Water Delivery Service Website

We are working with BrivoNessé. They are a water delivery company and in need of a new website design.
Some sites to use for inspiration:
https://www.pelmoriston.example/home
https://www.quintalbrook.example/en/home3
https://www.drevik.example
https://www.tormaxel.example
Thank you for taking the time to consider designing a website for us. We are web developers based in Stockton, CA, USA. Most of our projects go through the same process. Understanding this process may help you win a project with us. We custom-code all of our websites in-house. We don’t have any requirements as to what tools you use for your design, but we prefer Figma files. For any design that we label as four-stars, we send it to the client for review. The client picks the final design they want us to use. Once we complete this process, we will continue to show additional clients all the four-star sites and purchase them later. Your designs will have multiple chances to sell. For better chances of success, we ask that you follow these guidelines.
IMAGES:
If you use any images or icons in the design, we ask that you have a link to the asset so we can purchase the image/icon. Most of the designs we submit do not have the customer’s images on them unless they have some great images. Be creative; show us the feeling you are trying to portray with your image choices. Use any royalty-free site you choose. We subscribe to Vantrel and mainly use their images, but we can purchase images outside of Vantrel.
PLEASE NOTE: we will not submit designs to clients with watermarks on the images.
FONTS:
We ask that you identify the fonts used in the design. This can be done in a message if you want. We typically use Google Fonts and Vantrel Fonts.
CONTENT:
We're always open to different content and ideas. We often submit designs with stock images so the client can see our vision. We typically take pictures after the website launch to use their images with our vision. Lorem Ipsum is fine for paragraphs, but we ask that you write the headers in correct English. We want to be able to show the vision and identify the sections of the website.
INSPIRATION:
We typically add a couple of links in the brief of websites we like to help you get started in your design.
REVISIONS:
We do not often ask for revisions of the designs unless we see something in the design that may not appeal to the client. If there are slight changes that we want to make, we do that in the development process.
FEEDBACK:
We rarely give feedback on designs during the design process. We are working on many website projects and do not have the time to provide feedback. We usually respond if your request is well thought out and asks specific questions, but a note asking “feedback, please” usually goes unanswered.

```html
<!DOCTYPE html>
<html lang="en">
<head>
<meta charset="utf-8">
<title>BrivoNessé — Water Delivery</title>
<link href="https://fonts.googleapis.com/css2?family=Ubuntu:wght@400;500;700&display=swap" rel="stylesheet">
<style>
:root{
  --navy:#1d2466;
  --cyan:#1fa9e1;
  --sky:#38b3e6;
  --text:#5b5f6b;
  --white:#ffffff;
  --footer:#1e2567;
}
*{box-sizing:border-box;margin:0;padding:0}
html,body{width:1200px;height:3885px;overflow:hidden}
body{position:relative;font-family:'Ubuntu',sans-serif;background:var(--white);color:var(--text)}
.abs{position:absolute}
/* header */
.topbar{left:452px;top:0;width:748px;height:60px;background:var(--navy);clip-path:polygon(0 0,100% 0,100% 100%,28px 100%);color:#fff;font-size:17px}
.topbar-stripe{left:438px;top:0;width:40px;height:60px;background:var(--cyan);clip-path:polygon(0 0,35% 0,100% 100%,65% 100%)}
.contact-item{top:19px;display:flex;align-items:center;gap:9px}
.contact-sep{left:362px;top:16px;width:2px;height:24px;background:var(--cyan)}
.brand{display:flex;align-items:center;gap:12px;color:var(--navy);font-weight:500}
.brand-dot{border-radius:50%;background:var(--cyan)}
.header-brand{left:113px;top:44px;font-size:44px}
.header-brand .brand-dot{width:32px;height:32px}
.nav{left:456px;top:84px;display:flex;gap:48px;font-size:17px;color:var(--navy)}
.nav .active{color:var(--sky)}
/* hero */
.hero{left:0;top:124px;width:1200px;height:660px;background:linear-gradient(180deg,#5f8fb3 0%,#3f73a2 45%,#34659a 70%,#2e5b8c 100%)}
.hero-bottle{left:790px;top:62px;width:250px;height:470px;border-radius:40px 40px 30px 30px;background:linear-gradient(180deg,#6fa7d9,#2f7cc4)}
.hero-text{left:117px;color:#fff}
.welcome{top:263px;font-size:38px;font-weight:400}
.headline{top:318px;font-size:48px;font-weight:700;line-height:60px}
.tagline{top:452px;font-size:26px;font-weight:500}
.wave{left:0;top:640px}
/* buttons */
.btn{display:flex;align-items:center;gap:20px;height:47px;border-radius:24px;background:var(--cyan);color:#fff;font-size:14px;padding:0 24px 0 6px}
.btn-icon{width:36px;height:36px;border-radius:50%;background:#fff;display:flex;align-items:center;justify-content:center;flex:none}
.btn.outline{background:#fff;color:var(--navy);border:2px solid var(--cyan)}
.btn.outline .btn-icon{background:var(--navy)}
/* who */
.who-ring{left:110px;top:820px;width:506px;height:506px;border-radius:50%;background:var(--cyan)}
.who-photo{left:120px;top:830px;width:496px;height:496px;border-radius:50%;background:linear-gradient(135deg,#8b5a3c,#4a4a52 50%,#2e4660)}
.h2{color:var(--navy);font-weight:500;font-size:42px}
.rule{height:3px;width:64px;background:var(--cyan)}
.para{font-size:15.5px;line-height:21.5px;color:var(--text)}
/* services */
.center{left:0;width:1200px;text-align:center}
.card{width:306px;height:373px;border-radius:20px;background:#fff;box-shadow:0 4px 14px rgba(0,0,0,.16);overflow:hidden}
.card-img{position:absolute;left:0;top:0;width:306px;height:236px}
.card-curve{position:absolute;left:0;top:196px}
.card-badge{position:absolute;right:26px;top:182px;width:60px;height:60px;border-radius:50%;background:#fff;box-shadow:0 2px 8px rgba(0,0,0,.2);display:flex;align-items:center;justify-content:center}
.card-title{position:absolute;left:22px;top:255px;font-size:20px;font-weight:500;color:var(--navy)}
.card-desc{position:absolute;left:22px;top:290px;width:250px;font-size:12px;line-height:16px;color:var(--text)}
.card-more{position:absolute;left:22px;top:335px;font-size:17px;font-weight:500;color:var(--cyan)}
/* testimonials */
.testimonials{left:0;top:2153px;width:1200px;height:525px;background:linear-gradient(160deg,#4bbbec,#26a4de 50%,#3ab3e8)}
.arrow-box{width:47px;height:53px;border:2px solid #fff;display:flex;align-items:center;justify-content:center}
.avatar{left:553px;top:2322px;width:94px;height:94px;border-radius:50%;background:linear-gradient(180deg,#c9b7a4,#6b5a4c)}
.quote{left:185px;top:2438px;width:830px;text-align:center;color:#fff;font-size:17px;line-height:25.5px}
/* premium */
.premium-circle{left:585px;top:2824px;width:504px;height:504px;border-radius:50%;background:var(--cyan);box-shadow:14px -14px 0 var(--navy)}
.cooler{left:698px;top:2762px;width:205px;height:570px;border-radius:14px;background:linear-gradient(90deg,#d9dbdc,#f5f5f5 50%,#cfd1d2)}
.jug{left:873px;top:3052px;width:175px;height:312px;border-radius:40px 40px 30px 30px;background:linear-gradient(180deg,#9cc4e8,#6aa3d6)}
/* footer */
.footer{left:0;top:3399px;width:1200px;height:486px;background:var(--footer);color:#fff}
.footer-brand{left:113px;top:3506px;font-size:64px;color:#fff}
.footer-brand .brand-dot{width:60px;height:60px}
.subscribe{left:568px;top:3460px;font-size:26px;font-weight:500;line-height:32px;color:#fff}
.email-field{left:568px;top:3536px;width:516px;height:62px;border-radius:31px;background:#fff;display:flex;align-items:center;padding:0 22px;font-size:15px;color:var(--navy);font-weight:500}
.email-field .sep{position:absolute;right:66px;top:16px;width:1px;height:30px;background:#ccc}
.footer-rule{left:116px;top:3642px;width:968px;height:1px;background:#3a4391}
.footer-links{left:0;width:1200px;top:3676px;display:flex;justify-content:center;gap:50px;font-size:20px;color:#fff}
.socials{left:0;width:1200px;top:3733px;display:flex;justify-content:center;gap:10px}
.social{width:46px;height:46px;border-radius:50%;border:2px solid #fff}
.copyright{top:3814px;font-size:16px;color:#fff}
</style>
</head>
<body>

<!-- header -->
<div class="abs topbar-stripe"></div>
<div class="abs topbar">
  <div class="abs contact-item" style="left:64px">
    <svg width="18" height="14" viewBox="0 0 18 14"><rect x="0" y="0" width="18" height="14" rx="2" fill="#fff"/><path d="M1 1l8 7 8-7" stroke="#1d2466" stroke-width="1.6" fill="none"/></svg>
    Email Us: info@brivonesse.example
  </div>
  <div class="abs contact-sep"></div>
  <div class="abs contact-item" style="left:418px">
    <svg width="16" height="16" viewBox="0 0 24 24"><path fill="#fff" d="M6.6 10.8a15.1 15.1 0 006.6 6.6l2.2-2.2c.3-.3.7-.4 1-.2 1.1.4 2.3.6 3.6.6.6 0 1 .4 1 1V20c0 .6-.4 1-1 1A17 17 0 013 4c0-.6.4-1 1-1h3.5c.6 0 1 .4 1 1 0 1.3.2 2.5.6 3.6.1.3 0 .7-.2 1z"/></svg>
    Call Us: +1 555-014-2290
  </div>
</div>
<div class="abs brand header-brand"><span class="brand-dot"></span>BrivoNessé</div>
<nav class="abs nav">
  <span class="active">Home</span><span>About</span><span>Services</span><span>Pricing</span><span>Contact</span><span>Testimonials</span>
</nav>

<!-- hero -->
<section class="abs hero" role="img" aria-label="Photo of a large blue water bottle on river stones with misty mountains behind">
  <div class="abs hero-bottle"></div>
</section>
<svg class="abs wave" width="1200" height="170" viewBox="0 0 1200 170">
  <path d="M0 100 C120 20 300 40 480 70 C640 100 760 170 960 130 C1080 105 1160 80 1200 60 L1200 170 L0 170Z" fill="#1fa9e1"/>
  <path d="M0 118 C120 45 300 62 480 92 C640 122 760 175 960 155 C1080 142 1160 120 1200 100 L1200 170 L0 170Z" fill="#fff"/>
</svg>
<div class="abs hero-text welcome">Welcome To</div>
<div class="abs hero-text headline">Pure, Refreshing Water<br>Delivered Right to Your Door.</div>
<div class="abs hero-text tagline">Stay Hydrated. Stay Healthy</div>
<div class="abs btn" style="left:116px;top:511px">
  <span class="btn-icon"><svg width="14" height="18" viewBox="0 0 14 18"><path d="M7 0C7 0 0 8 0 11.5A7 7 0 0014 11.5C14 8 7 0 7 0z" fill="#1d2466"/></svg></span>Get Started
</div>

<!-- who we are -->
<div class="abs who-ring"></div>
<div class="abs who-photo" role="img" aria-label="Photo of two coworkers chatting beside an office water cooler"></div>
<h2 class="abs h2" style="left:659px;top:872px">Who We Are</h2>
<div class="abs rule" style="left:662px;top:926px"></div>
<p class="abs para" style="left:662px;top:942px;width:426px">Sed ut perspiciatis unde omnis iste natus error sit voluptatem accusantium doloremque laudantium, totam rem aperiam, eaque ipsa quae ab illo inventore veritatis et quasi architecto beatae vitae dicta sunt explicabo. Nemo enim ipsam voluptatem quia voluptas sit aspernatur aut odit aut fugit, sed quia consequuntur magni dolores eos qui ratione voluptatem sequi nesciunt.</p>
<p class="abs para" style="left:662px;top:1106px;width:426px">Sed ut perspiciatis unde omnis iste natus error sit voluptatem accusantium doloremque laudantium, totam rem aperiam, eaque ipsa quae ab illo inventore veritatis et quasi architecto beatae vitae dicta sunt explicabo.</p>
<div class="abs btn" style="left:666px;top:1211px">
  <span class="btn-icon"><svg width="14" height="18" viewBox="0 0 14 18"><path d="M7 0C7 0 0 8 0 11.5A7 7 0 0014 11.5C14 8 7 0 7 0z" fill="#1d2466"/></svg></span>Read More
</div>

<!-- services -->
<h2 class="abs h2 center" style="top:1414px">Our Services</h2>
<div class="abs rule" style="left:568px;top:1466px"></div>
<p class="abs center para" style="top:1497px;font-size:15px;line-height:22px">Sed ut perspiciatis unde omnis iste natus error sit voluptatem accusantium doloremque laudantium,<br>totam rem aperiam, eaque ipsa quae ab illo inventore veritatis et quasi architecto beatae</p>

<div class="abs card" style="left:110px;top:1574px">
  <div class="card-img" role="img" aria-label="Photo of a woman filling a glass at an office water dispenser" style="background:linear-gradient(180deg,#e7e8ea,#b9b3ab)"></div>
  <svg class="card-curve" width="306" height="60" viewBox="0 0 306 60"><path d="M0 30 C90 0 200 0 306 10 L306 60 L0 60Z" fill="#fff"/></svg>
  <div class="card-badge"><svg width="28" height="32" viewBox="0 0 14 18"><path d="M7 1C7 1 1 8 1 11.5A6 6 0 0013 11.5C13 8 7 1 7 1z" fill="none" stroke="#1d2466" stroke-width="1.2"/></svg></div>
  <div class="card-title">Pure &amp; Filtered</div>
  <div class="card-desc">Sed ut perspiciatis unde omnis iste natus error sit voluptatem accusantium</div>
  <div class="card-more">Read More &nbsp;»</div>
</div>
<div class="abs card" style="left:447px;top:1574px">
  <div class="card-img" role="img" aria-label="Photo of water being poured from a pitcher beside a large water bottle" style="background:linear-gradient(180deg,#dfe3e4,#9eb0bf)"></div>
  <svg class="card-curve" width="306" height="60" viewBox="0 0 306 60"><path d="M0 30 C90 0 200 0 306 10 L306 60 L0 60Z" fill="#fff"/></svg>
  <div class="card-badge"><svg width="28" height="32" viewBox="0 0 14 18"><path d="M7 1C7 1 1 8 1 11.5A6 6 0 0013 11.5C13 8 7 1 7 1z" fill="none" stroke="#1d2466" stroke-width="1.2"/></svg></div>
  <div class="card-title">Fast &amp; Reliable</div>
  <div class="card-desc">Sed ut perspiciatis unde omnis iste natus error sit voluptatem accusantium</div>
  <div class="card-more">Read More &nbsp;»</div>
</div>
<div class="abs card" style="left:784px;top:1574px">
  <div class="card-img" role="img" aria-label="Illustration of a green eco sphere with environmental icons over moss" style="background:linear-gradient(180deg,#3f7d3a,#7fb24a)"></div>
  <svg class="card-curve" width="306" height="60" viewBox="0 0 306 60"><path d="M0 30 C90 0 200 0 306 10 L306 60 L0 60Z" fill="#fff"/></svg>
  <div class="card-badge"><svg width="28" height="32" viewBox="0 0 14 18"><path d="M7 1C7 1 1 8 1 11.5A6 6 0 0013 11.5C13 8 7 1 7 1z" fill="none" stroke="#1d2466" stroke-width="1.2"/></svg></div>
  <div class="card-title">Eco-Friendly</div>
  <div class="card-desc">Sed ut perspiciatis unde omnis iste natus error sit voluptatem accusantium</div>
  <div class="card-more">Read More &nbsp;»</div>
</div>

<div class="abs btn" style="left:406px;top:2015px;padding-right:22px">
  <span class="btn-icon"><svg width="14" height="18" viewBox="0 0 14 18"><path d="M7 0C7 0 0 8 0 11.5A7 7 0 0014 11.5C14 8 7 0 7 0z" fill="#1d2466"/></svg></span>Water Solutions
</div>
<div class="abs btn outline" style="left:593px;top:2015px;padding-right:18px">
  <span class="btn-icon"><svg width="14" height="18" viewBox="0 0 14 18"><path d="M7 0C7 0 0 8 0 11.5A7 7 0 0014 11.5C14 8 7 0 7 0z" fill="#fff"/></svg></span>Commercial Services
</div>

<!-- testimonials -->
<section class="abs testimonials" role="img" aria-label="Background photo of rippling pool water"></section>
<h2 class="abs center h2" style="top:2228px;color:#fff;font-size:44px">Our Testimonials</h2>
<div class="abs rule" style="left:568px;top:2290px;background:var(--navy)"></div>
<div class="abs avatar" role="img" aria-label="Customer portrait photo"></div>
<div class="abs arrow-box" style="left:65px;top:2366px"><svg width="22" height="12" viewBox="0 0 22 12"><path d="M22 6H3M8 1L2 6l6 5" stroke="#fff" stroke-width="2.2" fill="none"/></svg></div>
<div class="abs arrow-box" style="left:1089px;top:2366px"><svg width="22" height="12" viewBox="0 0 22 12"><path d="M0 6h19M14 1l6 5-6 5" stroke="#fff" stroke-width="2.2" fill="none"/></svg></div>
<p class="abs quote">Sed ut perspiciatis unde omnis iste natus error sit voluptatem accusantium doloremque laudantium, totam rem aperiam, eaque ipsa quae ab illo inventore veritatis et quasi architecto beatae vitae dicta sunt explicabo. Nemo enim ipsam voluptatem quia voluptas sit aspernatur aut odit aut fugit, sed quia consequuntur magni dolores eos qui ratione voluptatem sequi nesciunt.</p>
<div class="abs center" style="top:2560px;font-size:25px;font-weight:500;color:var(--navy)">Maren Tolvik</div>

<!-- premium delivery -->
<h2 class="abs h2" style="left:111px;top:2858px;font-size:44px;line-height:52px">Premium Water Delivery<br>&nbsp;BrivoNessé to You</h2>
<div class="abs rule" style="left:116px;top:2970px"></div>
<p class="abs para" style="left:116px;top:3004px;width:426px">Sed ut perspiciatis unde omnis iste natus error sit voluptatem accusantium doloremque laudantium, totam rem aperiam, eaque ipsa quae ab illo inventore veritatis et quasi architecto beatae vitae dicta sunt explicabo. Nemo enim ipsam voluptatem quia voluptas sit aspernatur aut odit aut fugit, sed quia consequuntur magni dolores eos qui ratione voluptatem sequi nesciunt.</p>
<div class="abs btn" style="left:118px;top:3185px">
  <span class="btn-icon"><svg width="14" height="18" viewBox="0 0 14 18"><path d="M7 0C7 0 0 8 0 11.5A7 7 0 0014 11.5C14 8 7 0 7 0z" fill="#1d2466"/></svg></span>Read More
</div>
<div class="abs premium-circle"></div>
<div class="abs cooler" role="img" aria-label="Photo of a white freestanding water cooler"></div>
<div class="abs jug" role="img" aria-label="Photo of a large blue water jug"></div>

<!-- footer -->
<footer class="abs footer"></footer>
<div class="abs brand footer-brand"><span class="brand-dot"></span>BrivoNessé</div>
<div class="abs subscribe">Subscribe for<br>Updates and Special Offers</div>
<div class="abs email-field">Enter Email
  <span class="sep"></span>
  <svg style="position:absolute;right:28px;top:21px" width="20" height="20" viewBox="0 0 20 20"><path d="M19 1L1 9l7 2 2 7z" fill="#1d2466"/></svg>
</div>
<div class="abs footer-rule"></div>
<nav class="abs footer-links"><span>Home</span><span>Services</span><span>Contact</span><span>Privacy Policy</span></nav>
<div class="abs socials"><span class="social"></span><span class="social"></span><span class="social"></span><span class="social"></span><span class="social"></span></div>
<div class="abs center copyright">Copyrights 2025 Company Name All Rights Reserved</div>

</body>
</html>
```